Need Business Card for our Real Estate Business with Sales Executive's Picture

PANTONE 484 C ( RED)

PANTONE 2766 C ( BLUE

Industry/Entity Type

Real Estate

Contact Information for Business Card

Name, Mobile, email, & picture of Person
Agency Phone, address, Web address

Requirements
Must have
• Our Logo Colours, Agent Picture,

```html
<!DOCTYPE html>
<html lang="en">
<head>
<meta charset="utf-8">
<title>Solano Real Estate — Business Card</title>
<link rel="stylesheet" href="https://fonts.googleapis.com/css2?family=Cinzel:wght@500&family=Jost:wght@400&display=swap">
<style>
  :root {
    --stage: #1a1a1b;
    --brand-red: #8c1c26;
    --brand-navy: #1f2a5e;
    --navy-deep: #18214d;
    --paper: #ffffff;
    --paper-shade: #f1f1f3;
    --rule: #3a4577;
    --ink: #2a3468;
  }
  * { box-sizing: border-box; margin: 0; padding: 0; }
  html, body { width: 1200px; height: 864px; overflow: hidden; }
  body {
    background: var(--stage);
    display: flex;
    align-items: center;
    justify-content: center;
    gap: 40px;
  }
  .card {
    position: relative;
    width: 540px;
    height: 310px;
    overflow: hidden;
    border-radius: 2px;
    box-shadow: 0 12px 30px rgba(0,0,0,.55);
  }

  /* Front */
  .card-front { background: linear-gradient(160deg, var(--paper) 55%, var(--paper-shade)); }
  .agent-photo {
    position: absolute;
    left: 58px; top: 22px;
    width: 108px; height: 108px;
    border-radius: 50%;
    border: 2px solid var(--brand-navy);
    background: radial-gradient(circle at 50% 40%, #dfe3ec, #2b3f8a 75%);
  }
  .divider {
    position: absolute;
    left: 0; right: 0; top: 158px;
    height: 2px;
    background: var(--rule);
  }
  .brand-panel {
    position: absolute;
    left: 0; top: 170px;
    width: 222px; height: 104px;
    background: linear-gradient(135deg, #2b3770, var(--navy-deep));
    display: flex;
    align-items: center;
    justify-content: center;
  }
  .brand-name {
    font-family: "Cinzel", serif;
    font-weight: 500;
    color: var(--paper);
    font-size: 28px;
    letter-spacing: 2px;
  }
  .agent-name {
    position: absolute;
    left: 300px; top: 130px;
    font-family: "Cinzel", serif;
    font-weight: 500;
    font-size: 19px;
    color: var(--brand-red);
    letter-spacing: 1px;
  }
  .contact-list {
    position: absolute;
    left: 262px; top: 172px;
    list-style: none;
    font-family: "Jost", sans-serif;
    font-size: 14px;
    color: var(--ink);
    letter-spacing: .6px;
  }
  .contact-list li {
    display: flex;
    align-items: center;
    gap: 8px;
    height: 19px;
  }
  .contact-list svg { width: 11px; height: 11px; fill: var(--brand-red); flex: none; }
  .office-address {
    position: absolute;
    left: 262px; top: 254px;
    font-family: "Jost", sans-serif;
    font-style: normal;
    font-size: 14.5px;
    line-height: 18px;
    color: var(--brand-red);
    letter-spacing: .6px;
  }

  /* Back */
  .card-back { background: linear-gradient(160deg, #2b3770, var(--navy-deep)); }
  .back-band {
    position: absolute;
    left: 0; right: 0; top: 0;
    height: 96px;
    background: var(--brand-red);
  }
  .back-stripe {
    position: absolute;
    left: 0; right: 0; top: 96px;
    height: 14px;
    background: var(--paper);
  }
  .back-brand {
    position: absolute;
    left: 0; right: 0; top: 180px;
    text-align: center;
  }
  .back-brand .brand-name { font-size: 36px; }
</style>
</head>
<body>
  <section class="card card-front" aria-label="Business card front">
    <div class="agent-photo" role="img" aria-label="Portrait photo of the sales executive"></div>
    <div class="divider"></div>
    <div class="brand-panel"><span class="brand-name">SOLANO</span></div>
    <h1 class="agent-name">OWEN MARSH</h1>
    <ul class="contact-list">
      <li><svg viewBox="0 0 24 24"><path d="M6.6 10.8a15 15 0 0 0 6.6 6.6l2.2-2.2a1 1 0 0 1 1-.25 11.4 11.4 0 0 0 3.6.57 1 1 0 0 1 1 1V20a1 1 0 0 1-1 1A17 17 0 0 1 3 4a1 1 0 0 1 1-1h3.5a1 1 0 0 1 1 1c0 1.25.2 2.45.57 3.57a1 1 0 0 1-.25 1z"/></svg>(09) 555 0142</li>
      <li><svg viewBox="0 0 24 24"><path d="M7 1h10a2 2 0 0 1 2 2v18a2 2 0 0 1-2 2H7a2 2 0 0 1-2-2V3a2 2 0 0 1 2-2zm0 3v14h10V4zm5 15.5a1 1 0 1 0 0 2 1 1 0 0 0 0-2z"/></svg>027 555 0198</li>
      <li><svg viewBox="0 0 24 24"><path d="M2 5h20v14H2zm2 2v.5l8 5 8-5V7zm0 2.8V17h16V9.8l-8 5z"/></svg>owen@solanorealty.com</li>
      <li><svg viewBox="0 0 24 24"><path d="M12 2a10 10 0 1 0 0 20 10 10 0 0 0 0-20zm6.9 9h-3a15 15 0 0 0-1.3-5.6A8 8 0 0 1 18.9 11zM12 4.1c.9 1.3 1.8 3.6 1.9 6.9h-3.8c.1-3.3 1-5.6 1.9-6.9zM9.4 5.4A15 15 0 0 0 8.1 11h-3a8 8 0 0 1 4.3-5.6zM5.1 13h3a15 15 0 0 0 1.3 5.6A8 8 0 0 1 5.1 13zm6.9 6.9c-.9-1.3-1.8-3.6-1.9-6.9h3.8c-.1 3.3-1 5.6-1.9 6.9zm2.6-1.3a15 15 0 0 0 1.3-5.6h3a8 8 0 0 1-4.3 5.6z"/></svg>www.solanorealty.com</li>
    </ul>
    <address class="office-address">2210 Maple Avenue Suite 400<br>Brookfield, IL 60513</address>
  </section>

  <section class="card card-back" aria-label="Business card back">
    <div class="back-band"></div>
    <div class="back-stripe"></div>
    <div class="back-brand"><span class="brand-name">SOLANO</span></div>
  </section>
</body>
</html>
```